update of B2B website and conversion to single page

The current website needs to be modernized. I want what is commonly called a single page website. It is not actually a single page. See some examples here:
https://www.plivenor.example/
https://www.quorbel.example/
https://www.trindavex.example/
Most or all graphics will be replaced.
Please see the attached spreadsheet for a rough draft of the home page layout. Convert the existing website at https://www.zolvarin.example/ to a single page website. We will provide the page content. You will provide all of the design, graphics, development, production deployment. etc. The look and feel should be corporate, polished, premium.

```html
<!DOCTYPE html>
<html lang="en">
<head>
<meta charset="utf-8">
<title>Zolvarin Data</title>
<link href="https://fonts.googleapis.com/css2?family=Montserrat:wght@400;500;600;700&family=Open+Sans:wght@400;600&display=swap" rel="stylesheet">
<style>
:root{
  --yellow:#fbb917;
  --navy:#2b3a6e;
  --navy-dark:#243262;
  --blue:#1b2fb8;
  --ink:#222;
  --muted:#555;
  --light:#f4f4f4;
  --black:#0d0d0d;
  --white:#fff;
}
*{box-sizing:border-box;margin:0;padding:0}
html,body{width:1200px;height:3529px;overflow:hidden}
body{font-family:"Open Sans",Arial,sans-serif;color:var(--ink);background:var(--white);position:relative}
section,header,footer{position:absolute;left:0;width:1200px}
.abs{position:absolute}

/* header */
.site-header{top:0;height:101px;border-top:4px solid var(--yellow);background:var(--white)}
.brand{left:112px;top:26px;display:flex;align-items:center;gap:12px}
.brand-mark{width:36px;height:36px;border-radius:50%;background:var(--navy)}
.brand-name{font-family:"Montserrat",sans-serif;font-weight:700;font-size:30px;color:var(--navy)}
.nav{right:112px;top:44px;display:flex;gap:56px;font-family:"Montserrat",sans-serif;font-size:12px;font-weight:600;color:#222}
.nav .active{color:var(--yellow)}

/* hero */
.hero{top:101px;height:546px;background:linear-gradient(100deg,#0a1b8a 0%,#1530c9 55%,#1a36c4 100%)}
.hero-art{left:0;top:0;width:640px;height:546px;background:radial-gradient(ellipse at 45% 45%,#3fa0ff 0%,#1b45d6 40%,rgba(21,48,201,0) 75%)}
.hero h1{left:700px;top:168px;font-family:"Montserrat",sans-serif;font-weight:500;font-size:52px;color:var(--white);letter-spacing:1px}
.hero .tagline{left:700px;top:240px;font-family:"Montserrat",sans-serif;font-size:20px;font-weight:500;color:var(--yellow)}
.hero p{left:700px;top:288px;width:390px;font-size:12.5px;line-height:26px;color:var(--white)}
.btn-more{left:700px;top:386px;width:135px;height:48px;background:var(--yellow);color:var(--white);font-family:"Montserrat",sans-serif;font-weight:600;font-size:14px;display:flex;align-items:center;justify-content:center;border-radius:2px}

/* features band */
.features{top:647px;height:183px;background:var(--yellow)}
.feature{top:0;width:330px;text-align:center;color:var(--white)}
.feature .ring{width:90px;height:90px;border:2px solid var(--white);border-radius:50%;margin:14px auto 0;display:flex;align-items:center;justify-content:center}
.feature h3{margin-top:20px;font-family:"Montserrat",sans-serif;font-size:14px;font-weight:600;line-height:26px}
.divider{top:0;width:14px;height:183px}

/* section titles */
.sec-title{width:1200px;text-align:center;font-family:"Montserrat",sans-serif;font-weight:500;font-size:32px;color:var(--navy)}
.rule{height:3px;width:76px;background:var(--yellow)}
.rule.center{left:562px}

.services{top:830px;height:905px}
.services .intro{top:124px;width:1200px;text-align:center;font-size:12px;color:var(--ink)}
.art{border-radius:6px}
.block h2{font-family:"Montserrat",sans-serif;font-weight:600;font-size:27px;color:var(--navy)}
.block p{font-size:12px;line-height:26px;color:var(--muted)}
.ticks{list-style:none}
.ticks li{font-size:13.5px;color:var(--muted);height:33.5px;display:flex;align-items:center;gap:22px}
.ticks svg{flex:none}

/* connectors */
.connectors{top:1735px;height:555px;background:linear-gradient(180deg,var(--navy-dark),var(--navy))}
.connectors .sec-title{color:var(--white);top:40px}
.conn-card{top:130px;width:306px;height:375px;border:2px solid rgba(255,255,255,.75);background:rgba(255,255,255,.05)}
.conn-card .icon{position:absolute;left:120px;top:38px}
.conn-card h3{position:absolute;top:148px;width:100%;text-align:center;font-family:"Montserrat",sans-serif;font-weight:600;font-size:17px;color:var(--white);letter-spacing:.5px}
.conn-card ul{position:absolute;left:92px;top:186px;list-style:none}
.conn-card li{height:28px;display:flex;align-items:center;gap:22px;font-size:12px;color:var(--white)}

/* support */
.support{top:2290px;height:375px;background:var(--light)}
.support .sec-title{top:34px}
.sup-card{top:150px;width:309px;height:168px;background:var(--white);box-shadow:0 1px 3px rgba(0,0,0,.12);text-align:center}
.sup-icon{top:110px;width:104px;height:104px;border-radius:50%;display:flex;align-items:center;justify-content:center}
.sup-card h4{margin-top:82px;font-family:"Montserrat",sans-serif;font-weight:700;font-size:14px;color:var(--navy)}
.sup-card p{font-size:12.5px;color:var(--muted);line-height:20px;margin-top:2px}

/* contact */
.contact{top:2665px;height:545px;background:var(--white)}
.contact-photo{left:380px;top:0;width:820px;height:545px;background:linear-gradient(90deg,#ffffff 0%,#e8edf2 25%,#b9c9d8 60%,#8a9db2 100%)}
.contact .sec-title{top:68px;font-size:30px}
.contact .sub{top:116px;width:1200px;text-align:center;font-size:12px;color:var(--muted)}
.field{left:132px;width:362px;border:1px solid #cfcfcf;background:var(--white);font-size:12px;color:#444;padding:0 14px;display:flex;align-items:center}
.field.msg{align-items:flex-start;padding-top:12px}
.btn-submit{left:132px;top:3122px;width:108px;height:41px;background:var(--navy);color:var(--white);font-family:"Montserrat",sans-serif;font-weight:600;font-size:14px;display:flex;align-items:center;justify-content:center;border-radius:2px}

/* footer */
.site-footer{top:3210px;height:319px;background:var(--black);color:var(--white)}
.social{top:29px;left:389px;display:flex;gap:15px}
.social span{width:59px;height:59px;border:1.5px solid #777;border-radius:50%;display:flex;align-items:center;justify-content:center}
.contact-item{top:140px;display:flex;gap:18px;align-items:flex-start}
.contact-item .ic{width:52px;height:52px;border:1.5px solid #888;border-radius:50%;display:flex;align-items:center;justify-content:center;flex:none}
.contact-item h5{font-family:"Montserrat",sans-serif;font-weight:500;font-size:18px;margin-top:4px}
.contact-item p{font-family:"Montserrat",sans-serif;font-size:11.5px;line-height:20px}
.copyright{top:272px;width:1200px;text-align:center;font-size:12px}
</style>
</head>
<body>

<header class="site-header">
  <div class="brand abs"><span class="brand-mark"></span><span class="brand-name">Zolvarin Data</span></div>
  <nav class="nav abs">
    <span class="active">HOME</span><span>SERVICES</span><span>RICH CONNECTORS</span><span>SUPPORT</span><span>CONTACT US</span>
  </nav>
</header>

<section class="hero">
  <div class="hero-art abs" role="img" aria-label="Illustration of a glowing cloud database connected to laptop, desktop and mobile devices"></div>
  <h1 class="abs">ZOLVARIN</h1>
  <div class="tagline abs">Data Quality On Premise or In The Cloud</div>
  <p class="abs">QualiCore can be installed on premise, on your network, in your data center, or you can outsource server hardware and system management tasks with a deployment in the cloud</p>
  <div class="btn-more abs">READ MORE</div>
</section>

<section class="features">
  <div class="feature abs" style="left:106px">
    <div class="ring"><svg width="40" height="40" viewBox="0 0 40 40" fill="none" stroke="#fff" stroke-width="2"><path d="M20 6a8 8 0 0 1 8 8c0 6-8 14-8 14s-8-8-8-14a8 8 0 0 1 8-8z"/><circle cx="20" cy="14" r="3"/><path d="M8 26l-4 8h32l-4-8"/></svg></div>
    <h3>CLEANSE ADDRESSES<br>IN 5 MINUTES</h3>
  </div>
  <svg class="divider abs" style="left:434px" viewBox="0 0 14 183" preserveAspectRatio="none"><polygon points="0,0 14,0 4,183 0,183" fill="#d99a0c"/></svg>
  <div class="feature abs" style="left:435px">
    <div class="ring"><svg width="40" height="40" viewBox="0 0 40 40" fill="none" stroke="#fff" stroke-width="2"><rect x="8" y="6" width="20" height="28" rx="2"/><path d="M12 13h12M12 19h8M12 25h6"/><path d="M22 30l12-12 3 3-12 12-4 1z"/></svg></div>
    <h3>MATCH &amp; MERGE RECORDS<br>IN 10 MINUTES</h3>
  </div>
  <svg class="divider abs" style="left:763px" viewBox="0 0 14 183" preserveAspectRatio="none"><polygon points="0,0 14,0 4,183 0,183" fill="#d99a0c"/></svg>
  <div class="feature abs" style="left:770px">
    <div class="ring"><svg width="40" height="40" viewBox="0 0 40 40" fill="#fff"><circle cx="20" cy="10" r="4"/><circle cx="9" cy="28" r="4"/><circle cx="20" cy="28" r="4"/><circle cx="31" cy="28" r="4"/><path d="M19 14h2v6h10v4h-2v-2H21v2h-2v-2H11v2H9v-4h10z"/></svg></div>
    <h3>MASTER RECORDS IN<br>60 MINUTES</h3>
  </div>
</section>

<section class="services">
  <h2 class="sec-title abs" style="top:50px">OUR SERVICES</h2>
  <div class="rule center abs" style="top:100px"></div>
  <p class="intro abs">Zolvarin Data consultants are Customer Data experts. We provide high value services to solve your biggest data challenges.</p>

  <div class="art abs" style="left:210px;top:235px;width:315px;height:255px;background:linear-gradient(160deg,#2e3e52,#5b6d80 60%,#e9eef2)" role="img" aria-label="Illustration of server racks, a monitor with bar charts and database stacks"></div>
  <div class="block abs" style="left:597px;top:232px">
    <h2>DATA QUALITY</h2>
    <div class="rule" style="margin-top:16px;width:88px"></div>
    <p style="margin-top:20px">The Zolvarin Data team has uncommonly deep expertise in these specific areas.<br>This expertise is frequently the difference between success and failure.</p>
    <ul class="ticks" style="margin-top:16px">
      <li><svg width="12" height="10" viewBox="0 0 12 10"><path d="M1 5l3.5 3.5L11 1" stroke="#fbb917" stroke-width="2.2" fill="none"/></svg>Global Address Verification</li>
      <li><svg width="12" height="10" viewBox="0 0 12 10"><path d="M1 5l3.5 3.5L11 1" stroke="#fbb917" stroke-width="2.2" fill="none"/></svg>Data Cleansing/Enrichment</li>
      <li><svg width="12" height="10" viewBox="0 0 12 10"><path d="M1 5l3.5 3.5L11 1" stroke="#fbb917" stroke-width="2.2" fill="none"/></svg>Match and Merge</li>
    </ul>
  </div>

  <div class="block abs" style="left:222px;top:576px">
    <h2>MASTER DATA MANAGEMENT</h2>
    <div class="rule" style="margin-top:16px;width:88px"></div>
    <p style="margin-top:20px">The Zolvarin Data team has uncommonly deep expertise in these specific areas.<br>This expertise is frequently the difference between success and failure.</p>
    <ul class="ticks" style="margin-top:16px">
      <li><svg width="12" height="10" viewBox="0 0 12 10"><path d="M1 5l3.5 3.5L11 1" stroke="#fbb917" stroke-width="2.2" fill="none"/></svg>Integration</li>
      <li><svg width="12" height="10" viewBox="0 0 12 10"><path d="M1 5l3.5 3.5L11 1" stroke="#fbb917" stroke-width="2.2" fill="none"/></svg>Mastering</li>
      <li><svg width="12" height="10" viewBox="0 0 12 10"><path d="M1 5l3.5 3.5L11 1" stroke="#fbb917" stroke-width="2.2" fill="none"/></svg>Governance</li>
    </ul>
  </div>
  <div class="art abs" style="left:735px;top:565px;width:300px;height:280px;background:linear-gradient(160deg,#7cc3e6,#3a4d63 60%,#e9eef2)" role="img" aria-label="Illustration of a laptop with documents, cloud with gears and database stacks"></div>
</section>

<section class="connectors">
  <h2 class="sec-title abs">RICH CONNECTORS</h2>
  <div class="rule center abs" style="top:90px"></div>

  <div class="conn-card abs" style="left:112px">
    <svg class="icon" width="64" height="80" viewBox="0 0 64 80" fill="none" stroke="#fbb917" stroke-width="3"><rect x="6" y="4" width="52" height="72" rx="2"/><circle cx="32" cy="30" r="9"/><path d="M20 52c2-8 22-8 24 0M18 62h28"/></svg>
    <h3>APPLICATIONS</h3>
    <ul>
      <li><svg width="12" height="10" viewBox="0 0 12 10"><path d="M1 5l3.5 3.5L11 1" stroke="#fff" stroke-width="2.2" fill="none"/></svg>Trindavex CRM</li>
      <li><svg width="12" height="10" viewBox="0 0 12 10"><path d="M1 5l3.5 3.5L11 1" stroke="#fff" stroke-width="2.2" fill="none"/></svg>FieldPilot</li>
      <li><svg width="12" height="10" viewBox="0 0 12 10"><path d="M1 5l3.5 3.5L11 1" stroke="#fff" stroke-width="2.2" fill="none"/></svg>Sorvel</li>
      <li><svg width="12" height="10" viewBox="0 0 12 10"><path d="M1 5l3.5 3.5L11 1" stroke="#fff" stroke-width="2.2" fill="none"/></svg>Orvane Business Suite</li>
      <li><svg width="12" height="10" viewBox="0 0 12 10"><path d="M1 5l3.5 3.5L11 1" stroke="#fff" stroke-width="2.2" fill="none"/></svg>Mevrix Dynamics*</li>
      <li><svg width="12" height="10" viewBox="0 0 12 10"><path d="M1 5l3.5 3.5L11 1" stroke="#fff" stroke-width="2.2" fill="none"/></svg>Kelvane ERP*</li>
    </ul>
  </div>

  <div class="conn-card abs" style="left:447px">
    <svg class="icon" width="64" height="80" viewBox="0 0 64 80" fill="none" stroke="#fbb917" stroke-width="3"><ellipse cx="32" cy="14" rx="26" ry="9"/><path d="M6 14v52c0 5 12 9 26 9s26-4 26-9V14M6 31c0 5 12 9 26 9s26-4 26-9M6 48c0 5 12 9 26 9s26-4 26-9"/></svg>
    <h3>DATABASES</h3>
    <ul>
      <li><svg width="12" height="10" viewBox="0 0 12 10"><path d="M1 5l3.5 3.5L11 1" stroke="#fff" stroke-width="2.2" fill="none"/></svg>Orvane DB</li>
      <li><svg width="12" height="10" viewBox="0 0 12 10"><path d="M1 5l3.5 3.5L11 1" stroke="#fff" stroke-width="2.2" fill="none"/></svg>NovaSQL</li>
      <li><svg width="12" height="10" viewBox="0 0 12 10"><path d="M1 5l3.5 3.5L11 1" stroke="#fff" stroke-width="2.2" fill="none"/></svg>Mevrix SQL Engine</li>
      <li><svg width="12" height="10" viewBox="0 0 12 10"><path d="M1 5l3.5 3.5L11 1" stroke="#fff" stroke-width="2.2" fill="none"/></svg>PostaBase</li>
      <li><svg width="12" height="10" viewBox="0 0 12 10"><path d="M1 5l3.5 3.5L11 1" stroke="#fff" stroke-width="2.2" fill="none"/></svg>Iverton DB</li>
      <li><svg width="12" height="10" viewBox="0 0 12 10"><path d="M1 5l3.5 3.5L11 1" stroke="#fff" stroke-width="2.2" fill="none"/></svg>Terravault*</li>
    </ul>
  </div>

  <div class="conn-card abs" style="left:781px">
    <svg class="icon" width="64" height="80" viewBox="0 0 64 80" fill="none" stroke="#fbb917" stroke-width="3"><path d="M18 4h28l12 12v50H18z"/><path d="M6 16v60h40"/><path d="M26 26h22M26 36h22M26 46h22M26 56h16"/></svg>
    <h3>FILES</h3>
    <ul>
      <li><svg width="12" height="10" viewBox="0 0 12 10"><path d="M1 5l3.5 3.5L11 1" stroke="#fff" stroke-width="2.2" fill="none"/></svg>CSV</li>
      <li><svg width="12" height="10" viewBox="0 0 12 10"><path d="M1 5l3.5 3.5L11 1" stroke="#fff" stroke-width="2.2" fill="none"/></svg>Delimited</li>
      <li><svg width="12" height="10" viewBox="0 0 12 10"><path d="M1 5l3.5 3.5L11 1" stroke="#fff" stroke-width="2.2" fill="none"/></svg>Spreadsheet</li>
    </ul>
  </div>
</section>

<section class="support">
  <h2 class="sec-title abs">SUPPORT</h2>
  <div class="sup-card abs" style="left:112px"><h4>BATCH</h4><p>ON YOUR SCHEDULE</p></div>
  <div class="sup-card abs" style="left:446px"><h4>STREAMING</h4><p>ALWAYS IN SYNC</p></div>
  <div class="sup-card abs" style="left:779px"><h4>REAL TIME/INTERACTIVE</h4><p>AUTOCOMPLETE ANYTHING<br>SMART SEARCH</p></div>
  <div class="sup-icon abs" style="left:214px;background:var(--navy)"><svg width="56" height="50" viewBox="0 0 56 50" fill="none" stroke="#fff" stroke-width="2.2"><circle cx="28" cy="10" r="6"/><circle cx="14" cy="20" r="5"/><circle cx="42" cy="20" r="5"/><path d="M18 46V30a10 10 0 0 1 20 0v16M4 46V34a8 8 0 0 1 12-6M52 46V34a8 8 0 0 0-12-6"/></svg></div>
  <div class="sup-icon abs" style="left:548px;background:var(--yellow)"><svg width="56" height="50" viewBox="0 0 56 50" fill="none" stroke="#fff" stroke-width="2.2"><rect x="6" y="6" width="44" height="30" rx="2"/><path d="M20 44h16M28 36v8"/><circle cx="28" cy="21" r="7"/><path d="M28 14v7l5 3"/></svg></div>
  <div class="sup-icon abs" style="left:881px;background:var(--navy)"><svg width="56" height="50" viewBox="0 0 56 50" fill="none" stroke="#fff" stroke-width="2.2"><path d="M8 40a22 22 0 1 1 40 0"/><path d="M28 32l12-14"/><circle cx="28" cy="32" r="3"/><path d="M14 22l3 2M28 14v4M42 22l-3 2"/></svg></div>
</section>

<section class="contact">
  <div class="contact-photo abs" role="img" aria-label="Photo of a smiling man working on a laptop in a bright office"></div>
  <h2 class="sec-title abs">CONTACT US</h2>
  <p class="sub abs">Sed ut perspiciatis unde omnis iste natus error sit voluptatem accusantium doloremque laudantium</p>
</section>
<div class="field abs" style="top:2830px;height:42px">Name :</div>
<div class="field abs" style="top:2879px;height:42px">Email address :</div>
<div class="field abs" style="top:2928px;height:42px">Phone :</div>
<div class="field msg abs" style="top:2977px;height:125px">Message :</div>
<div class="btn-submit abs">SUBMIT</div>

<footer class="site-footer">
  <div class="social abs">
    <span aria-label="Share"><svg width="18" height="18" viewBox="0 0 18 18" fill="none" stroke="#fff" stroke-width="1.5"><circle cx="4" cy="9" r="2.5"/><circle cx="14" cy="3.5" r="2.5"/><circle cx="14" cy="14.5" r="2.5"/><path d="M6.2 8l5.6-3.2M6.2 10l5.6 3.2"/></svg></span>
    <span aria-label="Chat"><svg width="18" height="18" viewBox="0 0 18 18" fill="none" stroke="#fff" stroke-width="1.5"><path d="M2 3h14v9H7l-4 3v-3H2z"/></svg></span>
    <span aria-label="Website"><svg width="18" height="18" viewBox="0 0 18 18" fill="none" stroke="#fff" stroke-width="1.5"><circle cx="9" cy="9" r="7"/><path d="M2 9h14M9 2c3 3 3 11 0 14M9 2c-3 3-3 11 0 14"/></svg></span>
    <span aria-label="Profile"><svg width="18" height="18" viewBox="0 0 18 18" fill="none" stroke="#fff" stroke-width="1.5"><circle cx="9" cy="6" r="3.5"/><path d="M2.5 16c1-4 12-4 13 0"/></svg></span>
    <span aria-label="Link"><svg width="18" height="18" viewBox="0 0 18 18" fill="none" stroke="#fff" stroke-width="1.5"><path d="M7.5 10.5l3-3M8 5l1.5-1.5a3 3 0 0 1 4.2 4.2L12.2 9.2M10 13l-1.5 1.5a3 3 0 0 1-4.2-4.2L5.8 8.8"/></svg></span>
    <span aria-label="Email"><svg width="18" height="14" viewBox="0 0 18 14" fill="none" stroke="#fff" stroke-width="1.5"><rect x="1" y="1" width="16" height="12"/><path d="M1 1l8 7 8-7"/></svg></span>
  </div>
  <div class="contact-item abs" style="left:146px">
    <div class="ic"><svg width="16" height="20" viewBox="0 0 16 20" fill="#fff"><path d="M8 0a7 7 0 0 1 7 7c0 5-7 13-7 13S1 12 1 7a7 7 0 0 1 7-7z"/><circle cx="8" cy="7" r="2.5" fill="#0d0d0d"/></svg></div>
    <div><h5>Address :</h5><p>418 Harbor Vale<br>Suite 120 Lindenport, CA 90001</p></div>
  </div>
  <div class="contact-item abs" style="left:518px">
    <div class="ic"><svg width="18" height="14" viewBox="0 0 18 14" fill="none" stroke="#fff" stroke-width="1.5"><rect x="1" y="1" width="16" height="12"/><path d="M1 1l8 7 8-7"/></svg></div>
    <div><h5>Email</h5><p>info@zolvarin.example</p></div>
  </div>
  <div class="contact-item abs" style="left:866px">
    <div class="ic"><svg width="18" height="18" viewBox="0 0 18 18" fill="#fff"><path d="M4 1l3 4-2 2c1 2 4 5 6 6l2-2 4 3-2 3C8 17 1 10 1 4z"/></svg></div>
    <div><h5>Phone</h5><p>Mobile : (555) 010-4827</p></div>
  </div>
  <p class="copyright abs">© Copyright-2018 Zolvarin. All rights reserved</p>
</footer>

</body>
</html>
```